We are a doctors medical practice
I need the business card to be eye catching and memorable,
to reflect professionalism, yet also warmth and care

the numbers need to be easy to see, for the elderly

and the logo also in a location that is large enough to see and be eye catching

Back of card:
opening hours:
Mon- Fri 8.30am to 6pm
Sat 9am to 4pm

rows for appontments, date and time
Updates

HiĀ 

Modification to company name

BROOKVALE KINDRED HEALTH MEDICAL PRACTICE

Thanks
Marla

Reason: I am look for a unique design that also fulfils the design brief

I have attempted to post a .eps and .ai file of the logo

Target Market(s)

needs to appeal to the majority, mainly adults

Industry/Entity Type

Medical

Contact Information for Business Card

company name: Brookvale Kindred Health Medical Practice
Name: Dr Marla Tobrik-Vey
Qualifications: MBBS, Bsci(med), FRACGP, DCH, SH&FPA, Dip Derm
Address: Shop 3/41-43 Corrow St, Tallowmere 2168
Ph: 02 9184 3025
Fax: 02 9318 6042

Requirements
Nice to have
• I like balance
gold/ silver incorporated, as well as the other colours in the logo- but not limited to these colours
a "medical" feel
Should not have
• dark or strong colours

```html
<!DOCTYPE html>
<html lang="en">
<head>
<meta charset="utf-8">
<title>Brookvale Kindred Health Medical Practice – Business Card</title>
<link rel="stylesheet" href="https://fonts.googleapis.com/css2?family=Open+Sans:wght@400;600;700&display=swap">
<style>
  :root {
    --navy: #1b3a6b;
    --green: #6dbf45;
    --white: #ffffff;
    --ink: #1f1f1f;
    --backdrop: #ebe8e4;
    --silver-dark: #8e9094;
    --silver-mid: #b3b5b8;
    --silver-light: #f4f4f4;
    --ring-blue: #2aa3d8;
  }
  * { box-sizing: border-box; margin: 0; padding: 0; }
  html, body {
    width: 1200px; height: 900px; overflow: hidden;
    background: var(--backdrop);
    font-family: "Open Sans", Arial, sans-serif;
  }
  .sheet {
    width: 1200px; height: 900px;
    display: flex; flex-direction: column; align-items: center; justify-content: center;
    gap: 24px;
  }
  .card {
    position: relative;
    width: 680px; height: 416px;
    overflow: hidden;
    box-shadow: 0 4px 14px rgba(0,0,0,.18);
  }

  /* Front */
  .card--front { background: var(--white); }
  .card-art { position: absolute; inset: 0; }
  .top-band { fill: var(--navy); }
  .lower-field { fill: var(--green); }
  .name-tab-outline { fill: none; stroke: var(--ink); stroke-width: 2.5; }
  .brand {
    position: absolute; left: 36px; top: 84px; right: 24px;
    display: flex; align-items: center; gap: 14px;
  }
  .brand-mark {
    width: 62px; height: 62px; flex: none;
    border-radius: 50%; border: 4px solid var(--ring-blue);
  }
  .brand-name {
    color: var(--navy); font-weight: 700; font-size: 20.5px;
    letter-spacing: .1px; white-space: nowrap;
  }
  .doctor {
    position: absolute; left: 170px; width: 400px; top: 178px;
    text-align: center; color: var(--navy);
  }
  .doctor-name { font-size: 29px; font-weight: 700; line-height: 1.1; }
  .doctor-quals { font-size: 15.5px; font-weight: 600; line-height: 1.4; margin-top: 6px; }
  .contact {
    position: absolute; left: 40px; top: 300px;
    color: var(--navy); font-weight: 700; font-size: 21px; line-height: 1.45;
  }
  .contact-row { display: flex; }
  .contact-label { width: 110px; }

  /* Back */
  .card--back {
    background: linear-gradient(180deg, var(--silver-light) 0%, #e4e5e6 100%);
  }
  .hours-band {
    height: 104px; padding: 18px 30px;
    background: linear-gradient(180deg, var(--silver-mid) 0%, var(--silver-dark) 100%);
    color: var(--white); font-size: 22px; font-weight: 600; line-height: 1.35;
    display: flex; gap: 18px;
  }
  .hours-title { letter-spacing: .5px; }
  .appointments { padding: 14px 36px 0; color: var(--ink); }
  .appointments-head {
    display: flex; justify-content: space-between; align-items: flex-end;
    font-size: 15px; font-weight: 600; margin-bottom: 4px;
  }
  .appointment-row {
    height: 32px; border-bottom: 2px dotted var(--ink);
  }
</style>
</head>
<body>
<main class="sheet">

  <section class="card card--front" aria-label="Business card front">
    <svg class="card-art" viewBox="0 0 680 416" aria-hidden="true">
      <rect class="top-band" x="0" y="0" width="680" height="62"/>
      <path class="lower-field"
            d="M0 240 L150 240 Q165 240 172 262 Q182 292 215 292 L560 292 Q588 292 596 250 Q602 218 630 218 L680 218 L680 416 L0 416 Z"/>
      <path class="name-tab-outline"
            d="M150 248 L150 200 Q150 170 182 170 L575 170 Q600 170 606 192 L610 214"/>
    </svg>

    <div class="brand">
      <span class="brand-mark"></span>
      <span class="brand-name">BROOKVALE KINDRED HEALTH MEDICAL PRACTICE</span>
    </div>

    <div class="doctor">
      <p class="doctor-name">Dr Marla Tobrik-Vey</p>
      <p class="doctor-quals">MBBS, Bsci(med), FRACGP,<br>DCH, SH&amp;FPA, Dip Derm</p>
    </div>

    <div class="contact">
      <p class="contact-row"><span class="contact-label">Tel</span><span>: 02 9184 3025</span></p>
      <p class="contact-row"><span class="contact-label">Fax</span><span>: 02 9318 6042</span></p>
      <p class="contact-row"><span class="contact-label">Address:</span><span>Shop 3/41-43 Corrow St, Tallowmere 2168</span></p>
    </div>
  </section>

  <section class="card card--back" aria-label="Business card back">
    <header class="hours-band">
      <span class="hours-title">OPENING HOURS:</span>
      <span>Mon- Fri 8.30am to 6pm<br>Sat 9am to 4pm</span>
    </header>
    <div class="appointments">
      <div class="appointments-head">
        <span>Appontments</span>
        <span>Date &amp; Time</span>
      </div>
      <div class="appointment-row"></div>
      <div class="appointment-row"></div>
      <div class="appointment-row"></div>
      <div class="appointment-row"></div>
      <div class="appointment-row"></div>
      <div class="appointment-row"></div>
      <div class="appointment-row"></div>
      <div class="appointment-row"></div>
    </div>
  </section>

</main>
</body>
</html>
```